Personal Trainer website design

We are working with a personal trainer to design a website. They offer their primary services: Diet Coaching, In-Person Coaching (workouts), and Remote Coaching.
Some sites we like: https://www.mirabelthorne.com, https://kavialune.com/en-us, https://corvexfit.co.uk
Thank you for taking the time to consider designing a website for us. We are web developers based in Stockton, CA USA. Most of our projects go through the same process. Understanding this process may help you win a project with us. We custom-code all of our websites in-house. We don’t have any requirements as to what tools you use for your design, but ask that you follow these guidelines.
IMAGES:
We ask that if you use any images, or icons in the design, have a link to the asset, so we can purchase the image/icon. Most of the designs we submit do not have the customer’s images on them unless they have some great images. Be creative; show us the feeling that you are trying to portray with your image choices. Use any royalty-free site you choose. We subscribe to Quillon and mostly use their images, but are ok to purchase images outside of Quillon.
FONTS:
We ask that you identify the fonts you’re using in the design. This can be done in a message if you want. We typically use Brivane Fonts and Quillon Fonts.
CONTENT:
We're always open to different content and ideas. Often, we submit designs with stock images so that the client can see our vision. We typically go back and take pictures after the website launch to use their images with our vision. Lorem Ipsum is fine for paragraphs, but we ask that you make the Headers with correct English. We want to be able to show the vision and identify the sections of the website.
INSPIRATION:
We try and add a couple of links in the brief of some websites that we like to help you get started in your design.
REVISIONS:
We do not often ask for revisions of the designs unless we see something in the design that may not appeal to the client. If there are slight changes that we want to make, we simply do that in the development process.
FEEDBACK:
We rarely give feedback on designs during the design process. We are working on many website projects and do not have the time to give feedback. We usually respond if your request is well thought out and asks specific questions, but a note asking “feedback, please” usually goes unanswered.
1 page

```html
<!DOCTYPE html>
<html lang="en">
<head>
<meta charset="utf-8">
<title>Stellafit – Personal Training</title>
<link href="https://fonts.googleapis.com/css2?family=Audiowide&family=Roboto:wght@400;500;700&display=swap" rel="stylesheet">
<style>
:root{
  --green:#7f8c14;
  --green-dark:#6a7610;
  --green-light:#9aa825;
  --ink:#222222;
  --dark:#232323;
  --text:#555555;
  --muted:#666666;
  --white:#ffffff;
}
*{margin:0;padding:0;box-sizing:border-box}
html,body{width:1200px;height:3111px;overflow:hidden}
body{position:relative;font-family:'Roboto',Arial,sans-serif;color:var(--ink);background:var(--white)}
.abs{position:absolute}
.display{font-family:'Audiowide','Roboto',sans-serif;font-weight:400;letter-spacing:1px}
.btn{position:absolute;display:flex;align-items:center;justify-content:center;border-radius:30px;font-weight:700;font-size:16px;color:var(--white);text-transform:uppercase}
.btn-dark{background:var(--ink)}
.btn-green{background:var(--green)}

/* header */
.site-header{position:absolute;left:0;top:0;width:1200px;height:138px;border-top:4px solid var(--green);background:var(--white)}
.brand{position:absolute;display:flex;align-items:center;gap:12px;font-family:'Roboto',sans-serif;font-weight:700;font-size:40px;line-height:48px;color:var(--ink);letter-spacing:1px}
.brand-dot{width:30px;height:30px;border-radius:50%;background:var(--green)}
.main-nav a{position:absolute;top:88px;font-size:16px;font-weight:500;color:var(--ink);text-decoration:none}

/* hero */
.hero{position:absolute;left:0;top:138px;width:1200px;height:553px;background:linear-gradient(120deg,#8a9818 0%,#7a8714 55%,#6f7c12 100%);overflow:hidden}
.hero-title{position:absolute;left:110px;top:92px;font-size:68px;line-height:80px;color:var(--white)}
.hero-text{position:absolute;left:112px;top:264px;width:480px;font-size:16px;line-height:26px;color:var(--white)}
.hero-photo{position:absolute;left:659px;top:56px;width:428px;height:428px;border-radius:50%;background:radial-gradient(circle at 55% 40%,#d7b89c 0%,#b33a2d 38%,#5a5a58 70%,#3a3a3a 100%)}
.hero-curve{position:absolute;left:0;top:0}

/* services */
.section-title{position:absolute;left:0;width:1200px;text-align:center;font-size:44px;color:var(--ink)}
.section-lead{position:absolute;left:160px;width:880px;text-align:center;color:var(--text)}
.service{position:absolute;width:340px;height:340px;border-radius:50%;background:var(--white);box-shadow:0 4px 14px rgba(0,0,0,.18);padding:9px}
.service-inner{position:relative;width:100%;height:100%;border-radius:50%;overflow:hidden}
.service-photo{position:absolute;inset:0}
.service-band{position:absolute;left:12%;right:12%;top:62%;height:60%;border-radius:50% 50% 0 0/30% 30% 0 0;background:var(--ink);display:flex;flex-direction:column;align-items:center;padding-top:16px;color:var(--white);font-weight:700;font-size:16px}
.service-band svg{margin-bottom:8px}
.service.is-active .service-band{background:var(--green);left:8%;right:8%;top:55%}

/* about */
.about{position:absolute;left:0;top:1463px;width:1200px;height:502px;background:linear-gradient(90deg,#262626,#1f1f1f)}
.about-art{position:absolute;left:110px;top:40px;width:430px;height:430px}
.about-title{position:absolute;left:595px;top:72px;font-size:44px;line-height:56px;color:var(--white)}
.about-text{position:absolute;left:601px;top:140px;width:480px;font-size:13.5px;line-height:26.5px;color:var(--white)}

/* testimonials */
.testimonial{position:absolute;top:2233px;width:474px;height:385px;background:var(--white);box-shadow:0 2px 12px rgba(0,0,0,.12);border-radius:4px;text-align:center}
.testimonial .quote-mark{position:absolute;left:217px;top:48px}
.testimonial p{position:absolute;left:46px;right:46px;top:104px;font-size:13px;line-height:25px;color:var(--muted)}
.testimonial .name{position:absolute;left:0;width:100%;top:294px;font-size:17px;font-weight:500;color:var(--ink)}
.testimonial .place{position:absolute;left:0;width:100%;top:324px;font-size:13px;color:var(--muted)}

/* footer */
.site-footer{position:absolute;left:0;top:2720px;width:1200px;height:391px}
.footer-brand{position:absolute;left:0;top:172px;width:1200px;display:flex;justify-content:center}
.footer-brand .brand{position:static;color:var(--white)}
.footer-nav{position:absolute;top:257px;font-size:16px;color:var(--white)}
.social{position:absolute;top:288px;width:26px;height:26px;border-radius:50%;background:var(--green)}
.copyright{position:absolute;left:0;width:1200px;top:338px;text-align:center;font-size:12px;color:var(--white)}
</style>
</head>
<body>

<header class="site-header">
  <div class="brand" style="left:110px;top:40px"><span class="brand-dot"></span><span>STELLAFIT</span></div>
  <div class="btn btn-dark" style="left:917px;top:18px;width:170px;height:47px">Get a Quote</div>
  <nav class="main-nav">
    <a style="left:575px">Home</a>
    <a style="left:663px">About Us</a>
    <a style="left:772px">Services</a>
    <a style="left:877px">Testimonials</a>
    <a style="left:1012px">Contact Us</a>
  </nav>
</header>

<section class="hero">
  <h1 class="hero-title display">WELCOME TO<br>STELLAFIT</h1>
  <p class="hero-text">It is a long established fact that a reader will be distracted by the readable content of a page when looking at its layout. The point of using Lorem Ipsum is that it has</p>
  <div class="btn btn-dark" style="left:112px;top:372px;width:196px;height:60px">Contact Us</div>
  <div class="hero-photo" role="img" aria-label="Athlete in a red tank top curling a dumbbell in the gym"></div>
  <svg class="hero-curve" width="1200" height="553" viewBox="0 0 1200 553">
    <path d="M0 553 L0 553 Q520 480 880 486 Q1130 490 1200 553 Z" fill="#ffffff"/>
  </svg>
</section>

<section class="services">
  <h2 class="section-title display" style="top:756px">OUR SERVICES</h2>
  <p class="section-lead" style="top:824px;font-size:12px;line-height:26px">It is a long established fact that a reader will be distracted by the readable content of a page when looking at its layout. The point of using Lorem Ipsum is that it has a more-or-less normal distribution of letters, as opposed to using 'Content here</p>
  <div class="btn btn-dark" style="left:515px;top:901px;width:170px;height:46px">Get Started</div>

  <div class="service" style="left:82px;top:952px">
    <div class="service-inner">
      <div class="service-photo" role="img" aria-label="Woman enjoying a fresh salad" style="background:linear-gradient(135deg,#c98a3e,#e8c27e 45%,#6f5338)"></div>
      <div class="service-band">
        <svg width="42" height="42" viewBox="0 0 42 42" fill="none" stroke="#fff" stroke-width="2"><rect x="6" y="6" width="24" height="30" rx="2"/><path d="M12 14h12M12 20h12M12 26h8"/><circle cx="32" cy="30" r="6"/></svg>
        Diet Coaching
      </div>
    </div>
  </div>

  <div class="service is-active" style="left:430px;top:1030px">
    <div class="service-inner">
      <div class="service-photo" role="img" aria-label="Trainer coaching a client lifting a barbell" style="background:linear-gradient(135deg,#d8d8d8,#8a8a8a 50%,#3b3b3b)"></div>
      <div class="service-band">
        <svg width="44" height="44" viewBox="0 0 44 44" fill="none" stroke="#fff" stroke-width="2"><circle cx="22" cy="14" r="8"/><path d="M8 40c0-9 6-14 14-14s14 5 14 14z"/></svg>
        In-Person Coaching
        <svg width="24" height="24" viewBox="0 0 24 24" style="margin-top:10px"><circle cx="12" cy="12" r="11" fill="#fff"/><path d="M10 7l5 5-5 5" stroke="#7f8c14" stroke-width="2.2" fill="none"/></svg>
      </div>
    </div>
  </div>

  <div class="service" style="left:776px;top:952px">
    <div class="service-inner">
      <div class="service-photo" role="img" aria-label="Smiling coach holding a tablet in a gym" style="background:linear-gradient(135deg,#e9eef2,#7dc3cf 50%,#3f7a6a)"></div>
      <div class="service-band">
        <svg width="44" height="42" viewBox="0 0 44 42" fill="none" stroke="#fff" stroke-width="2"><rect x="6" y="6" width="32" height="22" rx="2"/><path d="M16 36l6-8 6 8M12 14h10M12 20h16"/></svg>
        Remote Coaching
      </div>
    </div>
  </div>
</section>

<section class="about">
  <div class="about-art" role="img" aria-label="Mascot illustration of an astronaut planting a flag" style="border-radius:50%;background:radial-gradient(circle at 40% 45%,#9aa825 0%,#7f8c14 60%,#6a7610 100%)"></div>
  <h2 class="about-title display">ABOUT US</h2>
  <p class="about-text">It is a long established fact that a reader will be distracted by the readable content of a page when looking at its layout. The point of using Lorem Ipsum is that it has a more-or-less normal distribution of letters, as opposed to using 'Content here, content here', making it look like readable English. Many desktop publishing packages and web page editors now use Lorem Ipsum as their default model text, and a search for 'lorem ipsum' will uncover many web sites still in their infancy. Various versions have evolved over the years, sometimes by accident, sometimes</p>
  <div class="btn btn-green" style="left:601px;top:375px;width:136px;height:46px">Read More</div>
</section>

<section class="testimonials">
  <h2 class="section-title display" style="top:2072px">HAPPY CUSTOMERS</h2>
  <p class="section-lead" style="top:2141px;left:150px;width:900px;font-size:15px;line-height:26px;color:var(--muted)">Lorem Ipsum is simply dummy text of the printing and typesetting industry. Lorem Ipsum has been the industry's standard dummy text ever since the 1500s, when an unknown printer took a galley of type and scrambled</p>

  <article class="testimonial" style="left:111px">
    <svg class="quote-mark" width="40" height="34" viewBox="0 0 40 34" fill="#222"><path d="M0 34V18Q0 4 12 0l3 5Q8 9 8 16h8v18zM22 34V18Q22 4 34 0l3 5Q30 9 30 16h8v18z"/></svg>
    <p>It is a long established fact that a reader will be distracted by the readable content of a page when looking at its layout. The point of using Lorem Ipsum is that it has a more-or-less normal distribution of letters, as opposed to using 'Content here, content here', making it look like readable English. Many desktop publishing packages and web page editors now use Lorem Ipsum as their default model text</p>
    <div class="name">- Daniel Reyes</div>
    <div class="place">Fernhollow, KS</div>
  </article>
  <article class="testimonial" style="left:614px">
    <svg class="quote-mark" width="40" height="34" viewBox="0 0 40 34" fill="#222"><path d="M0 34V18Q0 4 12 0l3 5Q8 9 8 16h8v18zM22 34V18Q22 4 34 0l3 5Q30 9 30 16h8v18z"/></svg>
    <p>It is a long established fact that a reader will be distracted by the readable content of a page when looking at its layout. The point of using Lorem Ipsum is that it has a more-or-less normal distribution of letters, as opposed to using 'Content here, content here', making it look like readable English. Many desktop publishing packages and web page editors now use Lorem Ipsum as their default model text</p>
    <div class="name">- Daniel Reyes</div>
    <div class="place">Fernhollow, KS</div>
  </article>

  <div class="btn btn-green" style="left:532px;top:2660px;width:136px;height:47px">View More</div>
</section>

<footer class="site-footer">
  <svg class="abs" style="left:0;top:0" width="1200" height="391" viewBox="0 0 1200 391">
    <path d="M0 7 Q600 70 1200 7 L1200 391 L0 391 Z" fill="#232323"/>
  </svg>
  <div class="footer-brand"><div class="brand"><span class="brand-dot"></span><span>STELLAFIT</span></div></div>
  <span class="footer-nav" style="left:246px">Home</span>
  <span class="footer-nav" style="left:333px">|</span>
  <span class="footer-nav" style="left:383px">About Us</span>
  <span class="footer-nav" style="left:492px">|</span>
  <span class="footer-nav" style="left:541px">Services</span>
  <span class="footer-nav" style="left:645px">|</span>
  <span class="footer-nav" style="left:694px">Testimonials</span>
  <span class="footer-nav" style="left:828px">|</span>
  <span class="footer-nav" style="left:877px">Contact Us</span>
  <span class="social" style="left:529px"></span>
  <span class="social" style="left:568px"></span>
  <span class="social" style="left:606px"></span>
  <span class="social" style="left:644px"></span>
  <div class="copyright">© Copyright 2023 Stellafit | All Rights Reserved.</div>
</footer>

</body>
</html>
```